New Website for World Wide Charity (KOLVAN)

We need a dynamic web design for our brand new charity organisation that will be working worldwide. We will be funded by donations so need to attract people to donate.

What We Do
We work to optimise the wellbeing of the planet, the animals and all that live within. Our slogan is Achieving Vibrational Equilibrium.

We have included a Powerpoint document which may help you understand what we need, it is just an idea for structure and style, it is not set in stone so feel free to be as creative as you like!
Updates

Designs look the same

Target Market(s)

Adults 18+ with an interest in animal, environmental. Businesses that may like to support our natural world or already support our natural world.

Number of Pages Required

3 page

Colors

Designer to choose colors to be used in the design.

Requirements
Must have
• We need the website to be easy to use and understand.

Web pages will be Home, What We Do, Who We Are, Success Stories, What You Can Do (Blog section), Seek Help, Donate, Join.
Nice to have
• Natural feel, easy to navigate, Ideally the website will look natural and organic.

Natural colours, blues, greens, sand, gold, brown, grey, silver, Orange and yellow for impact.
Should not have
• Should not have a dark coloured theme.

```html
<!DOCTYPE html>
<html lang="en">
<head>
<meta charset="utf-8">
<title>Kolvan – Help Raise World Vibration</title>
<link href="https://fonts.googleapis.com/css2?family=Poppins:wght@400;500;600&family=Roboto+Condensed:wght@700;800&display=swap" rel="stylesheet">
<style>
:root{
  --green:#11664f;
  --green-dark:#0f5b4a;
  --teal:#7aafa5;
  --ink:#1f1f1f;
  --text:#3a3a3a;
  --muted:#9a9a9a;
  --light:#f6f6f6;
  --lavender:#ddd3e6;
  --navy:#23407a;
}
*{margin:0;padding:0;box-sizing:border-box}
html,body{width:1200px;height:3664px;overflow:hidden}
body{position:relative;font-family:'Poppins',sans-serif;color:var(--text);background:#fff}
.abs{position:absolute}
.cond{font-family:'Roboto Condensed',sans-serif;font-weight:800;text-transform:uppercase}

/* header */
.header{left:0;top:0;width:1200px;height:104px;background:#fff;box-shadow:0 2px 6px rgba(0,0,0,.08);z-index:5}
.brand{left:36px;top:12px;width:140px;height:130px;border-radius:50%;background:#fff;border:3px solid #5a7fb8;display:flex;align-items:center;justify-content:center;font-weight:600;font-size:20px;color:var(--navy);z-index:7}
.topbar{right:38px;top:9px;display:flex;gap:34px;font-size:12px;color:#555;align-items:center;z-index:6}
.topbar span{display:flex;align-items:center;gap:6px}
.dot{width:9px;height:9px;border-radius:50%;background:#999;display:inline-block}
.rule{left:240px;top:36px;width:960px;height:1px;background:#eee;z-index:6}
.nav{left:385px;top:54px;display:flex;align-items:center;font-size:13px;font-weight:600;color:var(--green);z-index:6}
.nav a{text-decoration:none;color:inherit;padding:0 18px;line-height:32px;white-space:nowrap}
.nav a.active{background:var(--green);color:#fff;padding:0 20px}
.nav a.btn{border:1px solid #ccc;color:#222;font-weight:500;font-size:12px;padding:0 22px;line-height:34px;margin-left:8px}

/* hero */
.hero{left:0;top:104px;width:1200px;height:661px;background:linear-gradient(180deg,#d3c3b8 0%,#d9d1ca 35%,#b9b7a3 60%,#55684a 85%,#3b4d36 100%)}
.hero-title{left:357px;top:272px;font-size:50px;line-height:52px;color:var(--ink)}
.hero-sub{left:357px;top:390px;font-size:22px;color:var(--green);font-family:'Roboto Condensed',sans-serif;font-weight:700}
.cta{left:357px;top:440px;width:216px;height:42px;background:var(--green);color:#fff;font-size:14px;display:flex;align-items:center;justify-content:center;font-weight:500}

/* cards */
.card{top:604px;width:321px;height:253px;background:#fff;padding:6px;box-shadow:0 2px 6px rgba(0,0,0,.1)}
.card .ph{width:100%;height:100%}
.card .label{position:absolute;bottom:6px;left:64px;width:200px;height:54px;background:#fff;display:flex;flex-direction:column;align-items:center;justify-content:center;font-size:25px;color:var(--navy)}
.card .label.on{background:var(--green);color:#fff;left:63px;height:76px;width:194px}
.label small{font-family:'Poppins',sans-serif;font-size:9px;font-weight:500;margin-top:4px}

/* feature sections */
.band-block{background:var(--teal)}
.dots{background-image:radial-gradient(#c8c8c8 1px,transparent 1.2px);background-size:8px 8px}
.feat-img{width:501px;height:398px}
.feat h2{font-size:27px;color:var(--green);position:absolute}
.ghost{position:absolute;font-family:'Roboto Condensed',sans-serif;font-weight:800;font-size:44px;color:#eeeeee;text-transform:uppercase}
.copy{position:absolute;width:410px;font-size:12.5px;line-height:20px;color:var(--text)}
.copy p{margin-bottom:19px}
.more{display:inline-flex;align-items:center;gap:5px;border:1.5px solid var(--green);color:var(--green);font-size:11px;padding:0 20px;height:32px;margin-top:10px;white-space:nowrap}

/* blog */
.blogs{left:0;top:2686px;width:1200px;height:607px;background:linear-gradient(180deg,#f8f5f2 0%,#f1efec 60%,#e4e6e1 100%)}
.blog-img{border:4px solid #fff;box-shadow:0 2px 6px rgba(0,0,0,.12)}
.date{display:inline-flex;align-items:center;gap:6px;color:var(--green);font-size:11px;font-weight:500;white-space:nowrap}
.small-title{font-size:13.5px;font-weight:500;color:var(--ink);line-height:20px}

/* footer */
.footer{left:0;top:3293px;width:1200px;height:330px;background:linear-gradient(180deg,var(--lavender) 0%,var(--lavender) 75%,#9e96b8 100%)}
.foot-logo{left:107px;top:3366px;width:156px;height:146px;border-radius:50%;border:3px solid #5a7fb8;display:flex;align-items:center;justify-content:center;font-size:20px;font-weight:600;color:var(--navy)}
.fcol h4{font-size:15px;font-weight:500;color:var(--green);margin-bottom:14px}
.fcol a{display:block;font-size:12px;color:#333;line-height:24px;text-decoration:none}
.contact-row{display:flex;gap:10px;font-size:12px;color:#333;line-height:18px;margin-bottom:16px}
.bottom{left:0;top:3623px;width:1200px;height:41px;background:var(--green-dark);color:#fff;font-size:12px;display:flex;align-items:center;justify-content:space-between;padding:0 100px 0 97px}
.socials{display:flex;gap:16px}
.socials i{width:9px;height:9px;border-radius:50%;background:#cfe3dd;display:block}
</style>
</head>
<body>

<!-- Header -->
<div class="abs header"></div>
<div class="abs brand">KOLVAN</div>
<div class="abs topbar">
  <span>
    <svg width="12" height="10" viewBox="0 0 12 10"><rect x=".5" y=".5" width="11" height="9" fill="#888"/><path d="M.5 .5l5.5 5 5.5-5" stroke="#fff" fill="none"/></svg>
    hello@kolvan.org
  </span>
  <span>
    <svg width="11" height="11" viewBox="0 0 24 24"><path fill="#888" d="M6.6 10.8a15 15 0 006.6 6.6l2.2-2.2a1 1 0 011-.25 11.4 11.4 0 003.6.6 1 1 0 011 1V20a1 1 0 01-1 1A17 17 0 013 4a1 1 0 011-1h3.5a1 1 0 011 1c0 1.25.2 2.45.6 3.6a1 1 0 01-.25 1z"/></svg>
    (555) 014-2087
  </span>
  <span style="gap:14px"><i class="dot"></i><i class="dot"></i><i class="dot" style="background:#222"></i><i class="dot"></i></span>
</div>
<div class="abs rule"></div>
<nav class="abs nav">
  <a class="active">Home</a>
  <a>What We Do</a>
  <a>Who We Are</a>
  <a>Success Stories</a>
  <a>What You Can Do</a>
  <a class="btn" style="margin-left:14px">DONATE</a>
  <a class="btn">JOIN</a>
</nav>

<!-- Hero -->
<section class="abs hero" role="img" aria-label="Misty pine forest at dawn"></section>
<h1 class="abs cond hero-title">Help Raise<br>World Vibration</h1>
<div class="abs hero-sub">Achieving Vibrational Equilibrium</div>
<div class="abs cta">MAKE A DIFFERENCE</div>

<div class="abs card" style="left:97px">
  <div class="ph" role="img" aria-label="Finger touching a green seedling" style="background:linear-gradient(135deg,#555 0%,#7b7b7b 50%,#6f8f3a 70%,#3a3a3a 100%)"></div>
  <div class="label cond">Environment</div>
</div>
<div class="abs card" style="left:439px">
  <div class="ph" role="img" aria-label="Child resting head against a dog through a fence" style="background:linear-gradient(135deg,#8a8a8a,#c9c9c9 50%,#5c5c5c)"></div>
  <div class="label cond">Animal</div>
</div>
<div class="abs card" style="left:781px">
  <div class="ph" role="img" aria-label="Volunteers serving a bowl of soup" style="background:linear-gradient(135deg,#9a8e86,#c7b8ae 40%,#8c7a70 70%,#6d5a4e)"></div>
  <div class="label on cond">Human<small>FIND OUT MORE →</small></div>
</div>

<!-- Environment -->
<div class="abs band-block" style="left:0;top:931px;width:186px;height:585px"></div>
<div class="abs dots" style="left:186px;top:985px;width:446px;height:280px"></div>
<div class="abs feat-img" role="img" aria-label="Finger touching a green seedling" style="left:98px;top:1021px;background:linear-gradient(135deg,#4a4a4a,#8a8a8a 45%,#6f9a38 60%,#2e2e2e)"></div>
<div class="feat">
  <div class="ghost" style="left:672px;top:1052px">Environment</div>
  <h2 class="cond" style="left:673px;top:1070px">Environment</h2>
</div>
<div class="copy" style="left:674px;top:1137px">
  <p>Lorem Ipsum is simply dummy text of the printing and typeset-ting industry.</p>
  <p>Lorem Ipsum has been the industry's standard dummy text ever since the 1500s, when an unknown printer took a galley of type and scrambled it to make a type specimen book.</p>
  <p>It has survived not only five centuries, but also the leap into electronic typesetting, remaining essentially unchanged.</p>
  <span class="more">Read More →</span>
</div>

<!-- Animal -->
<div class="abs" style="left:0;top:1516px;width:1200px;height:584px;background:var(--light)"></div>
<div class="abs band-block" style="left:1012px;top:1516px;width:188px;height:584px"></div>
<div class="abs dots" style="left:566px;top:1572px;width:446px;height:265px"></div>
<div class="abs feat-img" role="img" aria-label="Child resting head against a dog through a fence" style="left:601px;top:1607px;background:linear-gradient(135deg,#8d8d8d,#cfcfcf 45%,#5a5a5a)"></div>
<div class="feat">
  <div class="ghost" style="left:97px;top:1642px">Animal</div>
  <h2 class="cond" style="left:97px;top:1658px">Animal</h2>
</div>
<div class="copy" style="left:99px;top:1722px">
  <p>Lorem Ipsum is simply dummy text of the printing and typeset-ting industry.</p>
  <p>Lorem Ipsum has been the industry's standard dummy text ever since the 1500s, when an unknown printer took a galley of type and scrambled it to make a type specimen book.</p>
  <p>It has survived not only five centuries, but also the leap into electronic typesetting, remaining essentially unchanged.</p>
  <span class="more">Read More →</span>
</div>

<!-- Human -->
<div class="abs band-block" style="left:0;top:2100px;width:186px;height:586px"></div>
<div class="abs dots" style="left:186px;top:2155px;width:446px;height:280px"></div>
<div class="abs feat-img" role="img" aria-label="Volunteers serving a bowl of soup" style="left:98px;top:2191px;background:linear-gradient(135deg,#8e8078,#c8b7ab 40%,#a08a7a 65%,#5e4c40)"></div>
<div class="feat">
  <div class="ghost" style="left:672px;top:2222px">Human</div>
  <h2 class="cond" style="left:673px;top:2240px">Human</h2>
</div>
<div class="copy" style="left:674px;top:2307px">
  <p>Lorem Ipsum is simply dummy text of the printing and typeset-ting industry.</p>
  <p>Lorem Ipsum has been the industry's standard dummy text ever since the 1500s, when an unknown printer took a galley of type and scrambled it to make a type specimen book.</p>
  <p>It has survived not only five centuries, but also the leap into electronic typesetting, remaining essentially unchanged.</p>
  <span class="more">Read More →</span>
</div>

<!-- Blogs -->
<section class="abs blogs"></section>
<div class="ghost" style="left:580px;top:2736px;font-size:40px;color:#ebe7e3">Blogs</div>
<h2 class="abs cond" style="left:541px;top:2750px;font-size:27px;color:var(--green)">Blogs</h2>

<div class="abs blog-img" role="img" aria-label="Volunteer collecting plastic bottles on grass" style="left:100px;top:2837px;width:486px;height:251px;background:linear-gradient(135deg,#7fae3a,#4f7d2a 40%,#3a4a6a 60%,#5fa0e0 80%,#6fa43a)"></div>
<div class="abs" style="left:644px;top:2855px;font-size:10px;color:var(--green)">View All →</div>
<div class="abs" style="left:644px;top:2877px;width:300px;font-size:17px;font-weight:500;color:var(--ink);line-height:26px">Good vibes or bad vibes Which do you prefer?</div>
<div class="abs" style="left:644px;top:2942px;width:440px;font-size:12px;line-height:21px;color:var(--muted)">Lorem Ipsum is simply dummy text of the printing and typesetting in-dustry. Lorem Ipsum has been the industry's standard...</div>
<div class="abs" style="left:644px;top:3012px;display:flex;align-items:center;gap:36px">
  <span class="date"><svg width="13" height="13" viewBox="0 0 14 14"><rect x="1" y="2" width="12" height="11" fill="none" stroke="#11664f" stroke-width="1.5"/><path d="M1 5.5h12M4 0v3M10 0v3" stroke="#11664f" stroke-width="1.5"/></svg>08 Feb 2021</span>
  <span class="more" style="margin:0;height:30px">Read More →</span>
</div>

<div class="abs blog-img" role="img" aria-label="Glass globe on mossy ground" style="left:100px;top:3114px;width:179px;height:95px;background:linear-gradient(135deg,#3c4a1a,#9aa34a 50%,#556b1e)"></div>
<div class="abs small-title" style="left:303px;top:3120px;width:230px">Lorem Ipsum is simply dummy text of the printing...</div>
<div class="abs" style="left:303px;top:3170px;display:flex;align-items:center;gap:24px">
  <span class="date"><svg width="12" height="12" viewBox="0 0 14 14"><rect x="1" y="2" width="12" height="11" fill="none" stroke="#11664f" stroke-width="1.5"/><path d="M1 5.5h12M4 0v3M10 0v3" stroke="#11664f" stroke-width="1.5"/></svg>08 Feb 2021</span>
  <span class="more" style="margin:0;height:30px;padding:0 14px">Read More →</span>
</div>

<div class="abs blog-img" role="img" aria-label="Hands holding paper cut-out figures" style="left:613px;top:3114px;width:179px;height:95px;background:linear-gradient(135deg,#c76a5a,#f2d7a8 50%,#b35848)"></div>
<div class="abs small-title" style="left:816px;top:3120px;width:230px">Lorem Ipsum is simply dummy text of the printing...</div>
<div class="abs" style="left:816px;top:3170px;display:flex;align-items:center;gap:24px">
  <span class="date"><svg width="12" height="12" viewBox="0 0 14 14"><rect x="1" y="2" width="12" height="11" fill="none" stroke="#11664f" stroke-width="1.5"/><path d="M1 5.5h12M4 0v3M10 0v3" stroke="#11664f" stroke-width="1.5"/></svg>08 Feb 2021</span>
  <span class="more" style="margin:0;height:30px;padding:0 14px">Read More →</span>
</div>

<!-- Footer -->
<footer class="abs footer"></footer>
<div class="abs foot-logo">KOLVAN</div>
<div class="abs fcol" style="left:340px;top:3362px">
  <h4>Quick Links</h4>
  <a>Home</a><a>What We Do</a><a>Who We Are</a><a>Success Stories</a><a>What You Can Do</a>
</div>
<div class="abs fcol" style="left:543px;top:3362px">
  <h4>Get Involved</h4>
  <a>Join Us</a><a>Fundraise</a><a>Donate</a><a>Shop</a>
</div>
<div class="abs fcol" style="left:738px;top:3362px">
  <h4>Legal</h4>
  <a>Terms and Conditions</a><a>Cookies</a><a>Privacy Policy</a>
</div>
<div class="abs fcol" style="left:931px;top:3362px">
  <h4>Conatct info</h4>
  <div class="contact-row"><svg width="12" height="12" viewBox="0 0 24 24"><path fill="#222" d="M6.6 10.8a15 15 0 006.6 6.6l2.2-2.2a1 1 0 011-.25 11.4 11.4 0 003.6.6 1 1 0 011 1V20a1 1 0 01-1 1A17 17 0 013 4a1 1 0 011-1h3.5a1 1 0 011 1c0 1.25.2 2.45.6 3.6a1 1 0 01-.25 1z"/></svg>(555) 014-2087</div>
  <div class="contact-row"><svg width="12" height="10" viewBox="0 0 12 10" style="margin-top:4px"><rect width="12" height="10" fill="#222"/><path d="M0 0l6 5.5L12 0" stroke="#ddd3e6" fill="none"/></svg>hello@kolvan.org</div>
  <div class="contact-row"><svg width="12" height="16" viewBox="0 0 12 16" style="margin-top:6px"><path fill="#222" d="M6 0a6 6 0 00-6 6c0 4.5 6 10 6 10s6-5.5 6-10a6 6 0 00-6-6zm0 8.5A2.5 2.5 0 116 3.5a2.5 2.5 0 010 5z"/></svg><span>214 Cedar Hollow Rd<br>Pinecrest, OR 97000</span></div>
</div>
<div class="abs" role="img" aria-label="Silhouette of pine treeline" style="left:0;top:3560px;width:1200px;height:63px;background:linear-gradient(180deg,rgba(60,50,100,0) 0%,#3d3670 100%)"></div>
<div class="abs bottom">
  <span>Copyright © 2021 Kolvan. All Rights Reserved</span>
  <span class="socials"><i></i><i></i><i></i><i></i></span>
</div>

</body>
</html>
```